Heron Loan Partners Business Card

We need a business card design for our mortgage servicing company. In addition to servicing the loans of homeowners, we help homeowners with purchasing their homes and any mortgage refinancing. We would like to see designs that use the colors in the logo attached below (gold-ish yellow and navy blue), and any other design you deem fit! The design should communicate a simpler life with smart mortgages provided by Heron.

```html
<!DOCTYPE html>
<html lang="en">
<head>
<meta charset="utf-8">
<title>Heron Loan Partners – Business Card</title>
<link href="https://fonts.googleapis.com/css2?family=Open+Sans:wght@400;700&display=swap" rel="stylesheet">
<style>
  :root {
    --navy: #232056;
    --gold: #e3ac32;
    --white: #ffffff;
    --grey-text: #5a5a5a;
    --backdrop: #2b2b2d;
  }
  * { margin: 0; padding: 0; box-sizing: border-box; }
  html, body {
    width: 1200px; height: 874px; overflow: hidden;
    background: var(--backdrop);
    font-family: "Open Sans", Arial, sans-serif;
  }
  .stage { position: relative; width: 1200px; height: 874px; }
  .card {
    position: absolute; left: 290px; width: 620px; height: 360px;
    background: var(--white); border-radius: 22px; overflow: hidden;
    box-shadow: 0 14px 30px rgba(0,0,0,0.45);
  }
  .card--front { top: 50px; }
  .card--back { top: 460px; }

  .front-brand {
    position: absolute; top: 128px; left: 0; width: 100%;
    display: flex; justify-content: center; align-items: center; gap: 14px;
    color: var(--gold); font-weight: 700; font-size: 42px; line-height: 1;
  }
  .front-brand .mark {
    width: 16px; height: 16px; border-radius: 50%; background: var(--navy); flex: none;
  }
  .tagline {
    position: absolute; top: 262px; left: 0; width: 100%;
    text-align: center; color: var(--grey-text); font-size: 16px;
  }

  .back-brand {
    position: absolute; top: 36px; right: 36px;
    color: var(--gold); font-weight: 700; font-size: 38px; text-align: right;
    line-height: 1.1;
  }
  .back-band {
    position: absolute; left: 0; bottom: 0; width: 100%; height: 200px;
  }
  .contact-person {
    position: absolute; left: 30px; bottom: 40px; width: 260px; text-align: right;
    color: var(--white); font-size: 15px; line-height: 1.4;
  }
  .contact-person .name { color: var(--gold); font-weight: 700; font-size: 24px; margin-bottom: 2px; }
  .divider {
    position: absolute; left: 308px; bottom: 36px; width: 1px; height: 112px;
    background: var(--white);
  }
  .contact-lines {
    position: absolute; left: 326px; bottom: 34px; list-style: none;
    color: var(--white); font-size: 15px; line-height: 1.7;
  }
  .contact-lines li { display: flex; align-items: center; gap: 10px; }
  .contact-lines svg { width: 14px; height: 14px; fill: var(--gold); flex: none; }
</style>
</head>
<body>
<div class="stage">
  <section class="card card--front">
    <div class="front-brand"><span class="mark"></span>Heron Loan Partners</div>
    <p class="tagline">Smart home loans for an easier tomorrow</p>
  </section>

  <section class="card card--back">
    <div class="back-brand">Heron<br>Loan Partners</div>
    <svg class="back-band" viewBox="0 0 620 200" preserveAspectRatio="none" role="img" aria-label="Navy fish silhouette illustration rising across the lower card">
      <path d="M0 40 Q310 0 620 40 L620 200 L0 200 Z" fill="var(--navy)"/>
      <path d="M0 40 Q310 0 620 40" fill="none" stroke="var(--gold)" stroke-width="3"/>
    </svg>
    <div class="contact-person">
      <p class="name">Daniel Reyes</p>
      <p>President</p>
      <p>4120 Harbor View Road</p>
      <p>Portland, Maine 04101</p>
    </div>
    <div class="divider"></div>
    <ul class="contact-lines">
      <li><svg viewBox="0 0 16 16"><path d="M3 1l3 3-2 2c1 2 3 4 5 5l2-2 3 3-2 3C6 15 1 10 1 3z"/></svg>555-214-7730</li>
      <li><svg viewBox="0 0 16 16"><path d="M4 0h8v16H4zM5.5 2v10h5V2z"/></svg>555-382-9146</li>
      <li><svg viewBox="0 0 16 16"><path d="M0 3h16v10H0zM1.5 4.5L8 9l6.5-4.5z"/></svg>info@heronloanpartners.com</li>
      <li><svg viewBox="0 0 16 16"><circle cx="8" cy="8" r="7"/></svg>www.heronloanpartners.com</li>
    </ul>
  </section>
</div>
</body>
</html>
```